Climbing Gear Company Stationary Design

We need some new stationary to standardise our business.
We require:

Business Card
A4 Letterhead
With complements slip

Our business is a Distributor and retailer of rock climbing equipment throughout Australia.
We need to the stationary (business card in particular) to reflect this.

Target Market(s)

customers, other retail outlets, overseas manufacturers.

Industry/Entity Type

Business

Requirements
Must have
• company logo
website url- www.ridgetopgearworks.com.au
email - mark@ridgetopgearworks.com
Business Address: Unit 3, 14-16 Marlowe Street, Wattle Cove, WA, 2371
Phone: 0438 627 194
my Name (on Business card) - Gordon Pellimore
use of Blue colour in our logo

```html
<!DOCTYPE html>
<html lang="en">
<head>
<meta charset="utf-8">
<title>Ridgetop Gearworks – Business Card</title>
<link rel="stylesheet" href="https://fonts.googleapis.com/css2?family=Open+Sans:wght@400;600;800&display=swap">
<style>
  :root {
    --brand-blue: #2b4592;
    --ink-grey: #555a60;
    --rule-grey: #8a9099;
    --card-white: #ffffff;
    --backdrop: #ece8e2;
  }
  * { margin: 0; padding: 0; box-sizing: border-box; }
  html, body { width: 1200px; height: 483px; overflow: hidden; background: var(--backdrop); }
  body { font-family: "Open Sans", Arial, sans-serif; }
  .stage { position: relative; width: 1200px; height: 483px; }

  .card {
    position: absolute; top: 95px; width: 526px; height: 300px;
    background: var(--card-white);
  }
  .card--front { left: 57px; }
  .card--back { left: 612px; }

  .brand { position: absolute; left: 0; width: 100%; text-align: center; color: var(--brand-blue); }
  .brand__name {
    font-weight: 800; font-size: 31px; letter-spacing: 0.5px; line-height: 1;
    display: inline-flex; align-items: center; gap: 10px;
  }
  .brand__dot { width: 13px; height: 13px; border-radius: 50%; background: var(--brand-blue); }
  .brand__tagline {
    display: block; margin-top: 12px;
    font-weight: 400; font-size: 13px; letter-spacing: 2.8px;
  }
  .card--front .brand { top: 82px; }
  .card--back .brand { top: 120px; }

  .band {
    position: absolute; left: 0; top: 204px; width: 241px; height: 47px;
    background: var(--brand-blue); border-radius: 0 7px 7px 0;
    color: #fff; display: flex; align-items: center;
  }
  .band--name { font-weight: 600; font-size: 15px; padding-left: 36px; text-transform: uppercase; }
  .band--web { font-weight: 400; font-size: 12.5px; padding-left: 26px; }

  .contact {
    position: absolute; left: 258px; top: 177px; height: 98px;
    border-left: 1px solid var(--rule-grey); padding-left: 16px;
    font-size: 11px; line-height: 18px; color: var(--ink-grey); font-style: normal;
  }
  .contact__address { margin-bottom: 8px; }
  .contact__web strong { color: var(--brand-blue); font-weight: 400; }
</style>
</head>
<body>
<main class="stage">
  <section class="card card--front" aria-label="Business card front">
    <div class="brand">
      <span class="brand__name"><span class="brand__dot"></span>RIDGETOP GEARWORKS</span>
      <span class="brand__tagline">THE ROPE•THE CRAG•THE SUMMIT</span>
    </div>
    <div class="band band--name">Gordon Pellimore</div>
    <address class="contact">
      <div class="contact__address">Unit 3, 14-16 Marlowe Street<br>Wattle Cove, WA, 2371</div>
      <div>P : 0438 627 194</div>
      <div>E : mark@ridgetopgearworks.com</div>
      <div class="contact__web">W: www.<strong>ridgetopgearworks</strong>.com.au</div>
    </address>
  </section>

  <section class="card card--back" aria-label="Business card back">
    <div class="brand">
      <span class="brand__name"><span class="brand__dot"></span>RIDGETOP GEARWORKS</span>
      <span class="brand__tagline">THE ROPE•THE CRAG•THE SUMMIT</span>
    </div>
    <div class="band band--web">www.ridgetopgearworks.com.au</div>
  </section>
</main>
</body>
</html>
```